Label for a new chocolate snack

Hello. We are Meadow Treat Store. We are a new company making healthy chocolate snacks. We need Labels for our first product: Orva's Chocolate Dates,

We have two varieties:

1) dark chocolate

2) milk chocolate

The labels are 4 inches wide by 6 inches height. They are being printed on white glossy paper. They will be going on Kraft bags.

Here is the info we need on the labels:

Orva's
Chocolate Dates
Peanut Butter Center
Milk Chocolate
8g of Protein
Great Source of Energy
175g.

Orvas Chocolate Dates are targeted towards women who are 20-45 years of age.
Our goal is to create products that are healthy and taste good at the same time.

Finally, we will be adding more variations in the future, such as almond butter center, so being able to change the theme of the label to match the center filling would be good.

Thank you to everyone who will be submitting a design and good luck.

Target Market(s)

Woman, 20-40 years old, shop at gourmet grocery stores and health food stores

Colors

Designer to choose colors to be used in the design.

Requirements
Must have
• Orva's
• Chocolate Dates
• Peanut Butter Centre
• Milk Chocolate / Dark Chocolate
• 8g of Protein
• Great Source of Energy
• 175g.
• Back side of label must have everything contained in the pdfs i have attached.
• We are looking for a upscale chocolate look. That will still stand out on the shelf.
Should not have
• Main colors should not be brown, or black.

```html
<!DOCTYPE html>
<html lang="en">
<head>
<meta charset="UTF-8">
<title>Orva's Chocolate Dates – Milk Chocolate Label</title>
<link href="https://fonts.googleapis.com/css2?family=Oswald:wght@400;500;600&display=swap" rel="stylesheet">
<style>
  :root {
    --cream: #fdf1b8;
    --cream-light: #fff8d6;
    --swirl: #f9df7a;
    --swirl-soft: #fbe99c;
    --berry-red: #c7202b;
    --berry-tint: #f4c2a0;
    --cocoa: #5a2a16;
    --white: #ffffff;
    --photo-dark: #2e1308;
    --photo-mid: #6b3417;
    --photo-light: #a9652f;
  }
  * { margin: 0; padding: 0; box-sizing: border-box; }
  html, body { width: 800px; height: 1200px; overflow: hidden; background: var(--cream); }
  .label {
    position: relative;
    width: 800px;
    height: 1200px;
    overflow: hidden;
    background: var(--cream);
    font-family: "Oswald", "Arial Narrow", sans-serif;
  }
  .label__swirls { position: absolute; inset: 0; }
  .brand-name {
    position: absolute;
    left: 80px;
    top: 62px;
    font-size: 100px;
    font-weight: 500;
    line-height: 1;
    color: var(--cocoa);
    letter-spacing: 1px;
  }
  .product-title {
    position: absolute;
    left: 0; right: 0;
    top: 312px;
    text-align: center;
    font-size: 76px;
    font-weight: 500;
    color: var(--berry-red);
    letter-spacing: 1px;
    line-height: 1;
  }
  .variety-banner {
    position: absolute;
    left: 200px;
    top: 414px;
    width: 400px;
    height: 60px;
  }
  .variety-banner__text {
    position: absolute;
    inset: 0;
    display: flex;
    align-items: center;
    justify-content: center;
    font-size: 40px;
    font-weight: 500;
    color: var(--white);
    letter-spacing: 1px;
  }
  .filling-line {
    position: absolute;
    left: 0; right: 0;
    top: 490px;
    text-align: center;
    font-size: 36px;
    font-weight: 400;
    color: var(--berry-red);
    letter-spacing: 1px;
  }
  .energy-badge { position: absolute; left: 40px; top: 566px; width: 140px; height: 140px; }
  .protein-badge { position: absolute; left: 40px; top: 745px; width: 124px; height: 130px; }
  .protein-badge__value {
    position: absolute;
    left: 0; right: 0;
    top: 6px;
    height: 88px;
    display: flex;
    align-items: center;
    justify-content: center;
    font-size: 48px;
    font-weight: 600;
    color: var(--berry-red);
  }
  .protein-badge__caption {
    position: absolute;
    left: 0; right: 0;
    top: 100px;
    text-align: center;
    font-size: 15px;
    font-weight: 500;
    color: var(--berry-red);
    letter-spacing: 0.5px;
  }
  .product-photo {
    position: absolute;
    left: 205px;
    top: 628px;
    width: 560px;
    height: 470px;
    border-radius: 42% 46% 38% 44% / 40% 44% 46% 48%;
    background: radial-gradient(ellipse at 40% 45%, var(--photo-light) 0%, var(--photo-mid) 38%, var(--photo-dark) 78%);
  }
  .net-weight {
    position: absolute;
    left: 0; right: 0;
    top: 1140px;
    text-align: center;
    font-size: 28px;
    font-weight: 400;
    line-height: 1.2;
    color: var(--berry-red);
  }
</style>
</head>
<body>
<main class="label">
  <svg class="label__swirls" width="800" height="1200" viewBox="0 0 800 1200" aria-hidden="true">
    <path d="M0 260 C180 200 260 40 520 0 L0 0 Z" fill="var(--cream-light)"/>
    <path d="M440 0 C560 120 640 160 800 150 L800 0 Z" fill="var(--swirl-soft)"/>
    <path d="M800 300 C650 340 600 520 680 640 C720 700 780 720 800 720 Z" fill="var(--swirl)"/>
    <path d="M0 540 C120 520 160 640 120 760 C90 850 40 900 0 910 Z" fill="var(--swirl-soft)"/>
    <path d="M0 1200 L0 960 C160 980 220 1080 200 1200 Z" fill="var(--swirl)"/>
    <path d="M300 580 C420 540 520 600 560 700 C600 780 700 800 800 780 L800 860 C680 880 560 840 500 760 C450 690 380 640 300 650 Z" fill="var(--cream-light)"/>
  </svg>

  <div class="brand-name">Orva's</div>

  <h1 class="product-title">CHOCOLATE DATES</h1>

  <div class="variety-banner">
    <svg width="400" height="60" viewBox="0 0 400 60" aria-hidden="true">
      <polygon points="0,0 400,0 386,30 400,60 0,60 14,30" fill="var(--berry-red)"/>
      <polygon points="22,6 378,6 368,30 378,54 22,54 32,30" fill="none" stroke="var(--white)" stroke-width="2"/>
    </svg>
    <div class="variety-banner__text">MILK CHOCOLATE</div>
  </div>

  <p class="filling-line">PEANUT BUTTER CENTER</p>

  <svg class="energy-badge" viewBox="0 0 140 140" aria-label="Great source of energy badge" role="img">
    <defs>
      <path id="energy-arc" d="M22 78 A48 48 0 0 1 118 78"/>
    </defs>
    <text font-family="Oswald, sans-serif" font-size="13" font-weight="500" fill="var(--berry-red)" letter-spacing="0.5">
      <textPath href="#energy-arc" startOffset="50%" text-anchor="middle">GREAT SOURCE OF ENERGY</textPath>
    </text>
    <circle cx="70" cy="86" r="36" fill="none" stroke="var(--berry-red)" stroke-width="4"/>
    <circle cx="70" cy="86" r="26" fill="var(--berry-tint)" role="img" aria-label="Running figure icon"/>
  </svg>

  <div class="protein-badge">
    <svg width="124" height="100" viewBox="0 0 124 100" aria-hidden="true">
      <circle cx="62" cy="50" r="44" fill="none" stroke="var(--berry-red)" stroke-width="4"/>
    </svg>
    <div class="protein-badge__value">8g</div>
    <div class="protein-badge__caption">OF PROTEIN</div>
  </div>

  <div class="product-photo" role="img" aria-label="Photo of three milk chocolate covered dates, two cut open showing the peanut butter center"></div>

  <p class="net-weight">Net Wt.175g</p>
</main>
</body>
</html>
```